Business card design Needed for new logo / Construction business, home extensions and new builds

We need a business card design using our new logo files which i will attach to this project :)

We are a small construction business specialising in home extensions, new builds and property development. We are very ambitious and would appreciate professional and elegant designs for our new business card.

Very serious about using the services on MakerQuarry and recently acquired our new logo from here :)

Please get involved, i will feedback when i can as i am very busy but can respond daily, thanks

Target Market(s)

People that want to build onto their houses, new building developments or adding too their existing property

Industry/Entity Type

Construction

Contact Information for Business Card

Renwick Tolliver Construction, Lionel Ashby (Managing Director), Tel 07822254961, email - info@renwick-tolliver, www.renwick-tolliver.co.uk

Colors

Designer to choose colors to be used in the design.

Requirements
Must have
• I like a deep grey on the back please. A lot of you have provided black from and back, try mixing things up a little. The black looks cool 😎 Thanks

```html
<!DOCTYPE html>
<html lang="en">
<head>
<meta charset="utf-8">
<title>Renwick Tolliver Construction – Business Card</title>
<link rel="stylesheet" href="https://fonts.googleapis.com/css2?family=Open+Sans:wght@400;600;700;800&display=swap">
<style>
  :root{
    --stage:#232323;
    --card-front:#1d1d21;
    --card-back-light:#a3a8ad;
    --card-back-dark:#858b91;
    --gold:#e2a62a;
    --gold-light:#f6d37a;
    --gold-deep:#b87d14;
    --silver:#d9dadc;
    --white:#f4f4f4;
    --ink:#1d1d21;
  }
  *{box-sizing:border-box;margin:0;padding:0}
  html,body{width:1200px;height:780px;overflow:hidden;background:var(--stage)}
  body{font-family:"Open Sans",Arial,sans-serif;position:relative}
  .card{position:absolute;top:80px;width:354px;height:620px;border-radius:22px;overflow:hidden}
  .card--back{left:230px;background:linear-gradient(160deg,var(--card-back-light),var(--card-back-dark))}
  .back-pattern{position:absolute;inset:0;background:linear-gradient(135deg,#b4b8bd 0%,#8d9399 55%,#7f858b 100%)}
  .back-brand{position:absolute;top:30px;right:30px;display:flex;align-items:center;gap:6px;
    font-size:8px;font-weight:700;letter-spacing:.08em;color:var(--white);text-transform:uppercase}
  .back-brand .mark{width:12px;height:12px;background:var(--white)}
  .card--front{left:616px;background:var(--card-front);color:var(--white)}
  .brand{position:absolute;top:86px;left:0;right:0;text-align:center}
  .brand .mark{display:block;width:22px;height:22px;margin:0 auto 18px;background:var(--gold)}
  .brand-name{font-size:20px;font-weight:700;letter-spacing:.12em;color:var(--gold);text-transform:uppercase;line-height:1.3}
  .person{position:absolute;top:292px;left:38px}
  .person-name{font-size:31px;font-weight:800;line-height:1}
  .person-name .first{color:var(--silver)}
  .person-name .last{color:var(--gold)}
  .person-role{font-size:14px;font-weight:600;margin-top:6px;padding-left:60px}
  .dots{position:absolute;left:0;width:354px;height:34px}
  .dots--top{top:350px}
  .dots--bottom{top:492px}
  .contact{position:absolute;top:396px;left:58px;font-size:15px;line-height:1.5;font-weight:600}
  .address{position:absolute;top:536px;left:58px;font-size:15px;line-height:1.5;font-weight:600}
</style>
</head>
<body>

<section class="card card--back" aria-label="Card back">
  <div class="back-pattern" role="img" aria-label="Repeating company emblem pattern in silver on deep grey"></div>
  <div class="back-brand"><span class="mark"></span>Renwick Tolliver Construction</div>
</section>

<section class="card card--front" aria-label="Card front">
  <div class="brand">
    <span class="mark"></span>
    <div class="brand-name">Renwick Tolliver<br>Construction</div>
  </div>

  <div class="person">
    <div class="person-name"><span class="first">Lionel</span> <span class="last">Ashby</span></div>
    <div class="person-role">Managing Director</div>
  </div>

  <svg class="dots dots--top" viewBox="0 0 354 34" aria-hidden="true">
    <defs>
      <linearGradient id="goldFill" x1="0" y1="0" x2="1" y2="1">
        <stop offset="0" stop-color="#f6d37a"/><stop offset=".5" stop-color="#e2a62a"/><stop offset="1" stop-color="#b87d14"/>
      </linearGradient>
    </defs>
    <g fill="url(#goldFill)">
      <circle cx="30" cy="17" r="2"/><circle cx="42" cy="17" r="2.6"/><circle cx="56" cy="17" r="3.3"/>
      <circle cx="71" cy="17" r="4"/><circle cx="87" cy="17" r="4.7"/><circle cx="104" cy="17" r="5.4"/>
      <circle cx="122" cy="17" r="6"/>
      <circle cx="146" cy="17" r="12"/><circle cx="176" cy="17" r="12"/><circle cx="206" cy="17" r="12"/>
      <circle cx="231" cy="17" r="6"/><circle cx="249" cy="17" r="5.4"/><circle cx="266" cy="17" r="4.7"/>
      <circle cx="282" cy="17" r="4"/><circle cx="297" cy="17" r="3.3"/><circle cx="311" cy="17" r="2.6"/>
      <circle cx="324" cy="17" r="2"/>
    </g>
    <g fill="none" stroke="#1d1d21" stroke-width="1.6" stroke-linecap="round">
      <path d="M141 11c-1 3 1 8 5 11 2 1 3 1 5-1l-2-3-2 1c-2-1-3-3-4-5l1-1-1-3z" fill="#1d1d21" stroke="none"/>
      <rect x="169.5" y="12" width="13" height="10" rx="1"/><path d="M169.5 12l6.5 5 6.5-5"/>
      <circle cx="206" cy="17" r="6"/><path d="M200 17h12M206 11c-3 3-3 9 0 12M206 11c3 3 3 9 0 12"/>
    </g>
  </svg>

  <address class="contact" style="font-style:normal">
    0782 225 4961<br>
    info@renwick-tolliver.co.uk<br>
    www.renwick-tolliver.co.uk
  </address>

  <svg class="dots dots--bottom" viewBox="0 0 354 34" aria-hidden="true">
    <g fill="url(#goldFill)">
      <circle cx="30" cy="17" r="2"/><circle cx="44" cy="17" r="2.7"/><circle cx="60" cy="17" r="3.5"/>
      <circle cx="77" cy="17" r="4.3"/><circle cx="96" cy="17" r="5"/><circle cx="116" cy="17" r="5.8"/>
      <circle cx="137" cy="17" r="6.5"/>
      <circle cx="170" cy="17" r="12"/>
      <circle cx="203" cy="17" r="6.5"/><circle cx="224" cy="17" r="5.8"/><circle cx="244" cy="17" r="5"/>
      <circle cx="263" cy="17" r="4.3"/><circle cx="280" cy="17" r="3.5"/><circle cx="296" cy="17" r="2.7"/>
      <circle cx="310" cy="17" r="2"/>
    </g>
    <path d="M170 25c-4-5-6-8-6-11a6 6 0 0 1 12 0c0 3-2 6-6 11z" fill="#1d1d21"/>
    <circle cx="170" cy="14" r="2.2" fill="#e2a62a"/>
  </svg>

  <address class="address" style="font-style:normal">
    Harrow Lane, Eastfield<br>
    Northbrook, NB4 7QX
  </address>
</section>

</body>
</html>
```